Professional Single Page Website Design for Tollbrook Advisory

Tollbrook Advisory is a new business consultancy specializing in providing expert services to small businesses, primarily in the brick-and-mortar retail and food service sectors. We offer a range of services including franchise development and launch, due diligence, and construction management.

Currently, we have a basic website set up at www.tollbrookadvisory.example, but we need a professional touch to enhance its design and functionality.

Project Requirements:
- Single Page Design: For now, we need a single page design that effectively showcases who we are, our services, and contact information.
- Future Expansion: The design should be flexible and scalable for future expansion to include additional pages like specific service offerings, about us, and a dedicated contact page.
- Design Aesthetic: We are looking for a modern yet professional design that aligns with our brand identity.
- Logo: We have a logo that we like, which was also sourced from Pixel Bazaar. The logo files are attached to this project brief.

Key Sections to Include:
- Hero Section: An engaging introduction to Tollbrook Advisory with a strong visual impact.
- About Us: A brief overview of who we are and our mission.
- Team: Section for the profiles of the two principals.
- Services: A clear and concise presentation of our services, including franchise development, due diligence, and construction management.
- Contact Information: Easy-to-find contact details, including a form for inquiries.
- Call to Action: Encouraging visitors to get in touch with us for consultations or further information.

Design Considerations:
- Ensure the design is responsive and mobile-friendly.
- Include high-quality images and icons that complement our services and industry.
- We do not need development services, this is only a design project.

```html
<!DOCTYPE html>
<html lang="en">
<head>
<meta charset="utf-8">
<title>Tollbrook Advisory</title>
<link rel="stylesheet" href="https://fonts.googleapis.com/css2?family=Roboto:wght@400;500;700&family=Roboto+Condensed:wght@400;500&display=swap">
<style>
:root{
  --mint:#8bc6af;
  --mint-dark:#6fae97;
  --ink:#141414;
  --dark:#1d1f20;
  --grey:#7a7a7a;
  --white:#ffffff;
}
*{margin:0;padding:0;box-sizing:border-box}
html,body{width:1200px;height:3568px;overflow:hidden}
body{position:relative;background:var(--white);font-family:"Roboto",sans-serif;color:var(--ink)}
.abs{position:absolute}
.bg-shapes{position:absolute;left:0;top:0;width:1200px;height:3568px}

/* nav */
.brand{left:100px;top:22px;display:flex;align-items:center;gap:10px;color:var(--white);font-weight:500;font-size:20px}
.brand-dot{width:44px;height:44px;border-radius:50%;border:5px solid var(--mint)}
.nav{left:660px;top:0;display:flex;font-size:17px;color:var(--white)}
.nav a{display:block;padding:0 21px;line-height:74px;color:inherit;text-decoration:none}
.nav a.active{background:var(--mint);padding:0 10px}

/* hero */
.hero-lead{left:97px;top:132px;color:var(--white);font-size:40px;font-weight:400}
.hero-title{left:97px;top:182px;color:var(--white);font-size:58px;font-weight:700}
.hero-sub{left:101px;top:270px;width:480px;color:var(--white);font-size:26px;line-height:34px}
.hero-text{left:101px;top:356px;width:490px;color:#e8e8e8;font-size:12.5px;line-height:20px}
.btn{display:block;background:var(--mint);color:var(--white);font-weight:500;font-size:16px;text-align:center;border-radius:27px}
.hero-btn{left:101px;top:485px;width:147px;height:53px;line-height:53px}
.scroll-cue{left:572px;top:614px;width:66px;height:66px;border-radius:50%;background:var(--mint-dark);display:flex;align-items:center;justify-content:center}
.scroll-cue span{width:50px;height:50px;border-radius:50%;background:var(--mint);display:flex;align-items:center;justify-content:center}

/* section headings */
.eyebrow{left:0;width:1200px;text-align:center;font-size:34px;font-weight:400}
.section-title{left:0;width:1200px;text-align:center;font-size:42px;font-weight:500}
.on-dark{color:var(--white)}

.about-text{left:140px;top:862px;width:920px;text-align:center;font-size:12.5px;line-height:26px;color:var(--grey)}
.card{top:1000px;width:359px;height:303px;border-radius:12px;padding:14px 26px;text-align:center;color:var(--white)}
.card h3{font-size:30px;font-weight:500;margin-bottom:18px}
.card p{font-size:14px;line-height:25.7px}
.card-who{left:223px;background:var(--mint)}
.card-who h3{color:var(--ink)}
.card-mission{left:607px;background:var(--ink)}

/* services */
.services-panel{left:101px;top:1605px;width:999px;height:478px;border-radius:30px;background:var(--mint)}
.tab{top:1618px;width:182px;height:50px;border-radius:25px;background:var(--white);font-size:12.5px;line-height:17px;display:flex;align-items:center;justify-content:center;text-align:center;padding:0 12px}
.tab.active{background:var(--ink);color:var(--white)}
.service-photo{left:148px;top:1705px;width:407px;height:345px;border-radius:30px;background:linear-gradient(135deg,#c9b79a,#7b8b8e 55%,#3e5a6e)}
.service-title{left:597px;top:1702px;width:480px;font-size:40px;line-height:48px;font-weight:500}
.service-text{left:603px;top:1812px;width:450px;font-size:12.5px;line-height:20.5px;color:#23302b}
.service-text p+p{margin-top:20.5px}
.arrow-btn{top:1834px;width:42px;height:42px;border-radius:50%;background:var(--white);display:flex;align-items:center;justify-content:center}

/* team */
.member{top:2350px;width:483px;height:195px}
.member-pill{left:70px;top:0;width:413px;height:195px;border-radius:98px 98px 98px 98px;background:var(--ink)}
.member-frame{left:30px;top:29px;width:138px;height:138px;border-radius:30px;background:var(--mint);transform:rotate(45deg)}
.member-photo{left:44px;top:43px;width:110px;height:110px;border-radius:22px;transform:rotate(45deg);background:linear-gradient(135deg,#b6a89a,#6d7f8f)}
.member-body{left:222px;top:15px;width:252px;color:var(--white)}
.member-body h4{font-size:23px;font-weight:500}
.member-body .role{font-size:20px;margin-top:4px}
.member-body .bio{font-size:10.5px;line-height:16.5px;margin-top:10px}
.member-body .links{display:flex;gap:26px;font-size:11px;margin-top:12px;align-items:center}
.member-body .links span{display:flex;align-items:center;gap:6px}

/* contact */
.field{left:100px;width:495px;background:var(--white);border-radius:4px;font-size:19px;padding:12px 11px;color:#333}
.send-btn{left:96px;top:3218px;width:145px;height:50px;line-height:50px}
.info-icon{left:650px;width:74px;height:74px;border-radius:50%;border:2px solid var(--white);display:flex;align-items:center;justify-content:center}
.info-text{left:742px;font-family:"Roboto Condensed",sans-serif;color:var(--white);font-size:21px;line-height:36px}
.divider{left:100px;top:3324px;width:996px;height:2px;background:var(--mint)}
.foot-nav{left:98px;top:3378px;display:flex;gap:53px;color:var(--white);font-size:22px}
.socials{left:100px;top:3438px;display:flex;gap:10px}
.socials span{width:51px;height:51px;border-radius:50%;border:2px solid var(--white)}
.copyright{left:98px;top:3522px;color:var(--white);font-size:18px}
.foot-brand{left:730px;top:3385px;display:flex;align-items:center;gap:18px;color:var(--white);font-size:38px;font-weight:700;line-height:42px}
.foot-brand .mark{width:90px;height:90px;border-radius:50%;border:8px solid var(--mint)}
</style>
</head>
<body>

<svg class="bg-shapes" viewBox="0 0 1200 3568" aria-hidden="true">
  <defs>
    <linearGradient id="heroBg" x1="0" y1="0" x2="1" y2="1">
      <stop offset="0" stop-color="#2b2d2f"/><stop offset="0.5" stop-color="#3c4246"/><stop offset="1" stop-color="#22272b"/>
    </linearGradient>
    <linearGradient id="servBg" x1="0" y1="0" x2="1" y2="0">
      <stop offset="0" stop-color="#2a2c2d"/><stop offset="0.5" stop-color="#3a3e40"/><stop offset="1" stop-color="#25282a"/>
    </linearGradient>
    <linearGradient id="contactBg" x1="0" y1="0" x2="0" y2="1">
      <stop offset="0" stop-color="#1c1d1e"/><stop offset="1" stop-color="#2e3234"/>
    </linearGradient>
  </defs>
  <path role="img" aria-label="City towers seen from below" d="M0 0H1200V555Q600 735 0 555Z" fill="url(#heroBg)"/>
  <path role="img" aria-label="Construction workers on site" d="M0 1407H1200V1920Q600 2180 0 1920Z" fill="url(#servBg)"/>
  <path d="M0 2745Q600 2565 1200 2745V3568H0Z" fill="url(#contactBg)"/>
</svg>

<!-- header -->
<div class="abs brand"><span class="brand-dot"></span>Tollbrook Advisory</div>
<nav class="abs nav">
  <a class="active" href="#">Home</a><a href="#">About</a><a href="#">Services</a><a href="#">Team</a><a href="#">Contact</a>
</nav>

<!-- hero -->
<div class="abs hero-lead">Building Success in</div>
<h1 class="abs hero-title">Southern California</h1>
<p class="abs hero-sub">Expertise at Every Step: From Planning to Execution</p>
<p class="abs hero-text">At Tollbrook, we blend innovative strategies with local market expertise to guide your commercial real estate ventures. Whether you're launching a new restaurant, investing in retail spaces, or expanding a franchise, our dedicated team is here to turn your real estate aspirations into tangible success. Dive into a partnership that grows with you.</p>
<a class="abs btn hero-btn">Learn More</a>
<div class="abs scroll-cue"><span><svg width="22" height="14" viewBox="0 0 22 14"><path d="M3 3l8 8 8-8" fill="none" stroke="#111" stroke-width="4" stroke-linecap="round" stroke-linejoin="round"/></svg></span></div>

<!-- about -->
<div class="abs eyebrow" style="top:748px">ABOUT US</div>
<h2 class="abs section-title" style="top:792px">Tollbrook Advisory</h2>
<p class="abs about-text">Welcome to Tollbrook Advisory, your trusted partner in navigating the complexities of the real estate and small business markets. Founded by industry veterans Rafael Dunmore and Kevin Arlow, we specialize in providing comprehensive services tailored to the unique needs of our clients. Whether you're a franchisee, a new restaurant owner, or a commercial real estate investor, our expertise in due diligence, construction management, and investment property evaluation ensures you make informed, strategic decisions.</p>
<div class="abs card card-who">
  <h3>Who We Are</h3>
  <p>At Tollbrook Advisory, we are committed to your success. Our approach combines meticulous analysis, strategic insights, and personalized service to help you achieve your business goals. We pride ourselves on our ability to deliver results that exceed expectations, fostering long-term relationships built on trust and excellence.</p>
</div>
<div class="abs card card-mission">
  <h3>Our Mission</h3>
  <p>Discover how Tollbrook Advisory can support your business journey. Partner with us and experience the difference our dedication and expertise can make.<br>Discover how Tollbrook Advisory can support your business journey. Partner with us and experience the difference our dedication and expertise can make.</p>
</div>

<!-- services -->
<div class="abs eyebrow on-dark" style="top:1465px">OUR SERVICES</div>
<h2 class="abs section-title on-dark" style="top:1509px">Tollbrook Services</h2>
<div class="abs services-panel"></div>
<div class="abs tab" style="left:118px">Franchise Development &amp; Launch</div>
<div class="abs tab" style="left:313px">Due Diligence</div>
<div class="abs tab active" style="left:510px">Building &amp; Construction Management</div>
<div class="abs tab" style="left:705px">Investment Property Evaluation</div>
<div class="abs tab" style="left:901px">Market Analysis &amp; Feasibility Studies</div>
<div class="abs service-photo" role="img" aria-label="Builders reviewing plans on a laptop at a site table"></div>
<h3 class="abs service-title">Building &amp; Construction Management</h3>
<div class="abs service-text">
  <p>Our Building &amp; Construction Management Services oversee every aspect of your construction and development projects, from initial planning to final completion. We ensure projects stay on time and within budget, providing meticulous attention to detail and proactive problem-solving.</p>
  <p>Specializing in tenant improvements (TIs) and ground-up construction for small to mid-size commercial projects, we handle everything from permitting and contractor coordination to quality control and final inspections. Trust us to deliver successful projects that meet your specifications and exceed your expectations, ensuring a smooth and efficient construction process every step of the way.</p>
</div>
<div class="abs arrow-btn" style="left:80px"><svg width="14" height="18" viewBox="0 0 14 18"><path d="M10 2L3 9l7 7" fill="none" stroke="#111" stroke-width="3.5" stroke-linecap="round" stroke-linejoin="round"/></svg></div>
<div class="abs arrow-btn" style="left:1079px"><svg width="14" height="18" viewBox="0 0 14 18"><path d="M4 2l7 7-7 7" fill="none" stroke="#111" stroke-width="3.5" stroke-linecap="round" stroke-linejoin="round"/></svg></div>

<!-- team -->
<div class="abs eyebrow" style="top:2196px">OUR TEAM</div>
<h2 class="abs section-title" style="top:2240px">Our Leadership Team</h2>

<div class="abs member" style="left:100px">
  <div class="abs member-pill"></div>
  <div class="abs member-frame"></div>
  <div class="abs member-photo" role="img" aria-label="Portrait of Rafael Dunmore"></div>
  <div class="abs member-body">
    <h4>Rafael Dunmore</h4>
    <div class="role">Principal</div>
    <p class="bio">Rafael Dunmore brings almost 20 years of rich experience as a real estate investor and a pivotal role at one of southern California's largest real estate management firms, where he...</p>
    <div class="links"><span><svg width="10" height="10" viewBox="0 0 24 24"><path d="M6.6 10.8a15 15 0 006.6 6.6l2.2-2.2a1 1 0 011-.25 11.4 11.4 0 003.6.57 1 1 0 011 1V20a1 1 0 01-1 1A17 17 0 013 4a1 1 0 011-1h3.5a1 1 0 011 1c0 1.25.2 2.45.57 3.57a1 1 0 01-.25 1z" fill="#8bc6af"/></svg>Phone</span><span><svg width="11" height="9" viewBox="0 0 22 16"><rect width="22" height="16" rx="2" fill="#8bc6af"/><path d="M1 2l10 7 10-7" fill="none" stroke="#141414" stroke-width="2"/></svg>Email</span></div>
  </div>
</div>

<div class="abs member" style="left:617px">
  <div class="abs member-pill"></div>
  <div class="abs member-frame"></div>
  <div class="abs member-photo" role="img" aria-label="Portrait of Kevin Arlow"></div>
  <div class="abs member-body">
    <h4>Kevin Arlow</h4>
    <div class="role">Principal</div>
    <p class="bio">Kevin Arlow is a seasoned real estate expert with extensive experience in project and construction management, and a licensed real estate agent in California. Fluent in both English and Korean,...</p>
    <div class="links"><span><svg width="10" height="10" viewBox="0 0 24 24"><path d="M6.6 10.8a15 15 0 006.6 6.6l2.2-2.2a1 1 0 011-.25 11.4 11.4 0 003.6.57 1 1 0 011 1V20a1 1 0 01-1 1A17 17 0 013 4a1 1 0 011-1h3.5a1 1 0 011 1c0 1.25.2 2.45.57 3.57a1 1 0 01-.25 1z" fill="#8bc6af"/></svg>Phone</span><span><svg width="11" height="9" viewBox="0 0 22 16"><rect width="22" height="16" rx="2" fill="#8bc6af"/><path d="M1 2l10 7 10-7" fill="none" stroke="#141414" stroke-width="2"/></svg>Email</span></div>
  </div>
</div>

<!-- contact -->
<div class="abs eyebrow on-dark" style="top:2743px">CONTACT US</div>
<h2 class="abs section-title on-dark" style="top:2789px">Tollbrook Advisory</h2>

<div class="abs field" style="top:2883px;height:54px">Name</div>
<div class="abs field" style="top:2945px;height:54px">Email</div>
<div class="abs field" style="top:3006px;height:54px">Subject</div>
<div class="abs field" style="top:3068px;height:130px">Message</div>
<a class="abs btn send-btn">Send Now</a>

<div class="abs info-icon" style="top:2883px"><svg width="22" height="32" viewBox="0 0 22 32"><path d="M11 0C4.9 0 0 4.9 0 11c0 8.2 11 21 11 21s11-12.8 11-21C22 4.9 17.1 0 11 0zm0 15a4 4 0 110-8 4 4 0 010 8z" fill="#fff"/></svg></div>
<div class="abs info-text" style="top:2902px">&nbsp;88 Lantern Ridge Rd&nbsp; Suite 100<br>88 Lantern Ridge Rd, Calderon, CA 90000</div>
<div class="abs info-icon" style="top:3018px"><svg width="30" height="30" viewBox="0 0 24 24"><path d="M6.6 10.8a15 15 0 006.6 6.6l2.2-2.2a1 1 0 011-.25 11.4 11.4 0 003.6.57 1 1 0 011 1V20a1 1 0 01-1 1A17 17 0 013 4a1 1 0 011-1h3.5a1 1 0 011 1c0 1.25.2 2.45.57 3.57a1 1 0 01-.25 1z" fill="#fff"/></svg></div>
<div class="abs info-text" style="top:3037px;left:750px">+1 555-010-0199</div>
<div class="abs info-icon" style="top:3121px"><svg width="34" height="26" viewBox="0 0 22 16"><rect width="22" height="16" rx="2" fill="#fff"/><path d="M1 2l10 7 10-7" fill="none" stroke="#1c1d1e" stroke-width="2"/></svg></div>
<div class="abs info-text" style="top:3140px;left:753px">info@tollbrookadvisory.example</div>

<div class="abs divider"></div>
<nav class="abs foot-nav"><span>Home</span><span>About</span><span>Services</span><span>Team</span><span>Contact</span></nav>
<div class="abs socials" role="img" aria-label="Social media links"><span></span><span></span><span></span><span></span><span></span></div>
<div class="abs copyright">Tollbrook Advisory © 2024 All Right Reserved</div>
<div class="abs foot-brand"><span class="mark"></span><span>Tollbrook<br>Advisory</span></div>

</body>
</html>
```